Create a step-by-step donors pamphlet for VELTO church

I am looking to get a professionally design pamphlet that gives our donors easy steps to set up reoccurring donation through our give platform.

The ideal design should look professional and creative. No templates or weak AIs.

I've provided church logos and a text file which contains the content of the pamphlet we are trying to make.

Font styles to use
Sans Serif

Requirements
Must have
• Good branding

```html
<!DOCTYPE html>
<html lang="en">
<head>
<meta charset="utf-8">
<title>VELTO – Recurring Giving Pamphlet</title>
<link href="https://fonts.googleapis.com/css2?family=Arimo:wght@400;700&family=Roboto+Slab:wght@700;800&display=swap" rel="stylesheet">
<style>
  :root{
    --bg:#efefef;
    --sheet:#151515;
    --divider:#3a3a3a;
    --ink:#f2f2f2;
    --muted:#cfcfcf;
    --orange:#f07a24;
    --orange-deep:#e2561a;
    --card:#ffffff;
    --card-ink:#1d1d1d;
    --rule:#d9d9d9;
  }
  *{box-sizing:border-box;margin:0;padding:0}
  html,body{width:1200px;height:655px;overflow:hidden}
  body{background:var(--bg);font-family:"Arimo",Arial,sans-serif;position:relative}

  .pamphlet{position:absolute;left:128px;top:64px;width:959px;height:511px;background:var(--sheet);display:flex;overflow:hidden}
  .panel{position:relative;height:100%;border-right:1px solid var(--divider)}
  .panel:last-child{border-right:none}
  .panel--cover{width:239px}
  .panel--benefits{width:236px;padding:36px 22px 0 24px}
  .panel--steps{width:238px;padding:30px 16px 0 20px}
  .panel--invite{width:246px}

  /* wordmark: name only, one colour, one weight, one circle */
  .wordmark{position:absolute;left:0;right:0;display:flex;align-items:center;justify-content:center;gap:8px;color:var(--ink)}
  .wordmark__dot{width:14px;height:14px;border-radius:50%;background:var(--orange)}
  .wordmark__name{font-family:"Arimo",Arial,sans-serif;font-weight:400;letter-spacing:1px;line-height:1}
  .panel--cover .wordmark{top:222px}
  .panel--cover .wordmark__name{font-size:54px}
  .cover-art{position:absolute;left:55px;top:345px;width:130px;height:135px;border-radius:50% 50% 8px 8px;background:radial-gradient(ellipse at 50% 80%,#ffd23c 0%,#f59320 40%,#e2501a 75%,rgba(21,21,21,0) 100%)}

  /* benefits */
  .title{font-weight:700;color:var(--ink);font-size:19.5px;line-height:1.2;text-align:center}
  .rule{height:1px;background:var(--rule);margin:14px auto;width:130px}
  .checklist{list-style:none}
  .checklist li{position:relative;padding-left:20px;font-size:11.5px;line-height:1.35;color:var(--muted);margin-bottom:6px}
  .checklist li::before{content:"";position:absolute;left:0;top:2px;width:11px;height:11px;border:1.5px solid var(--orange);border-radius:2px}
  .checklist li::after{content:"";position:absolute;left:3px;top:3px;width:5px;height:8px;border:solid var(--orange);border-width:0 2px 2px 0;transform:rotate(40deg)}
  .label{font-family:"Roboto Slab",Georgia,serif;font-weight:800;color:var(--orange);font-size:10.5px;letter-spacing:.4px;text-transform:uppercase;margin-bottom:8px;white-space:nowrap}
  .label--center{text-align:center}
  .benefit-card{background:var(--card);border-radius:8px;padding:12px 14px 10px;margin-top:22px}
  .benefit-card .label{color:var(--orange-deep);text-align:center}
  .ticks{list-style:none}
  .ticks li{position:relative;padding-left:18px;font-size:11.5px;line-height:1.3;color:var(--card-ink);margin-bottom:7px}
  .ticks li::before{content:"";position:absolute;left:2px;top:1px;width:5px;height:9px;border:solid var(--orange);border-width:0 2px 2px 0;transform:rotate(40deg)}

  /* steps */
  .step{margin-bottom:16px}
  .step p{font-size:11.3px;line-height:1.4;color:var(--muted)}
  .step p em{font-style:normal;color:var(--orange)}
  .story{position:absolute;left:20px;top:368px;width:203px;height:82px;display:flex;background:#0f1a2c}
  .story__text{width:50%;padding:8px 6px;font-size:7px;line-height:1.4;color:var(--muted)}
  .story__text b{color:var(--orange)}
  .story__art{width:50%;background:linear-gradient(180deg,#2a4f86 0%,#1b2c4d 55%,#d8521c 100%)}

  /* invite */
  .window-art{position:absolute;left:50px;top:36px;width:150px;height:160px;border-radius:75px 75px 22px 22px;background:radial-gradient(circle at 50% 30%,#f2f2f2 0%,#8aa8d6 18%,#2b4a86 50%,#15243f 80%),#15243f;border:3px solid #2b2b2b}
  .accent{position:absolute;left:91px;top:213px;width:64px;height:2px;background:var(--orange)}
  .invite-copy{position:absolute;left:24px;top:233px;right:18px}
  .invite-copy h2{font-size:18px;font-weight:700;color:var(--ink);line-height:1.2;margin-bottom:8px}
  .invite-copy p{font-size:9.5px;line-height:1.4;color:var(--muted)}
  .dash{position:absolute;left:0;right:0;top:350px;border-top:1px dashed #6a6a6a}
  .panel--invite .wordmark{top:424px}
  .panel--invite .wordmark__name{font-size:40px}
  .corner{position:absolute;right:0;bottom:0}
</style>
</head>
<body>
  <main class="pamphlet">
    <section class="panel panel--cover">
      <div class="wordmark"><span class="wordmark__dot"></span><span class="wordmark__name">VELTO</span></div>
      <div class="cover-art" role="img" aria-label="Illustration of a bright orange and yellow flame"></div>
    </section>

    <section class="panel panel--benefits">
      <h1 class="title">Partner with VELTO in Building the Kingdom.</h1>
      <div class="rule"></div>
      <ul class="checklist">
        <li>Your steady gifts help us reach more homes, fund outreach and build lasting ministries.</li>
      </ul>
      <div class="rule"></div>
      <h3 class="label label--center">1 Main Benefit:</h3>
      <ul class="checklist">
        <li>Plan your giving once and support ministry monthly.</li>
        <li>No need to remember every week</li>
      </ul>
      <div class="benefit-card">
        <h3 class="label">Free Giving Benefit:</h3>
        <ul class="ticks">
          <li>Receive your giving record, tax ready.</li>
          <li>Reliable support for outreach and missions.</li>
          <li>Pause or change your gift at any time online.</li>
        </ul>
      </div>
    </section>

    <section class="panel panel--steps">
      <div class="step">
        <h3 class="label">1. Set up recurring today:</h3>
        <p>Set up your recurring gift in a few simple steps.</p>
      </div>
      <div class="step">
        <p>Set up a recurring donation on the Giving Page to support <em>ministries, outreach</em> and missions every month. <em>Choose an amount</em> and date that fits your plan.</p>
      </div>
      <div class="step">
        <h3 class="label">2. Once you're on the page</h3>
        <p>Open the form and choose monthly on the Giving Page.</p>
      </div>
      <div class="step">
        <h3 class="label">3. Repeat each month:</h3>
        <p>Pick your fund, enter your details and confirm. You will receive a receipt by email.</p>
      </div>
      <div class="story">
        <div class="story__text">When you give each month, your gift keeps the <b>fire of ministry</b> burning. Thank you for partnering with <b>VELTO</b>.</div>
        <div class="story__art" role="img" aria-label="Stained glass scene of a white dove above flames"></div>
      </div>
    </section>

    <section class="panel panel--invite">
      <div class="window-art" role="img" aria-label="Arched stained glass window with a white dove and rays of light over flames"></div>
      <div class="accent"></div>
      <div class="invite-copy">
        <h2>Are you a VELTO recurring donor yet?</h2>
        <p>Our church grows when everyone gives faithfully. Join the family of monthly partners.</p>
      </div>
      <div class="dash"></div>
      <div class="wordmark"><span class="wordmark__dot"></span><span class="wordmark__name">VELTO</span></div>
      <svg class="corner" width="62" height="66" viewBox="0 0 62 66" aria-hidden="true">
        <path d="M62 0 C48 6 52 20 40 26 C28 32 30 46 18 52 C10 56 4 60 0 66 L62 66 Z" fill="var(--orange)"/>
      </svg>
    </section>
  </main>
</body>
</html>
```